Website for enterprise software start-up

We need a new Wordpress website. We are an early stage start-up focused on mobile video technology for cellular operators. The audience is strategy, marketing and customer acquisition execs from the operators.

The purpose of the site is to act as a sales brochure and capture leads. A demo app can be downloaded from the current site, want to put that behind a contact form.

Current website is at www.velmora.tv. Similar number of pages. Looking for a clean design template, with minimal customization. Blog will remain as is.

Want to be able to modify the copy via Wordpress. Reference designs I like: quandrix.com, briskfold7metrics.com

Target Market(s)

Mobile operators and MVNOs in the US and Asia Pacific regions

Industry/Entity Type

Business Software

Coding

Coded - Design and coding required

Number of Pages Required

4 page

Font styles to use
Sans Serif

Colors
f78f20

Requirements
Must have
• Form for downloading sample apps.
• Landing page with image, Product, Blog, About, Contact
• Team page

```html
<!DOCTYPE html>
<html lang="en">
<head>
<meta charset="utf-8">
<title>Velmora Media – Mobile Video Engagement</title>
<link rel="stylesheet" href="https://fonts.googleapis.com/css2?family=Raleway:wght@400;500;600;700&display=swap">
<style>
:root{
  --orange:#f78f20;
  --orange-dark:#e2781a;
  --ink:#333;
  --muted:#666;
  --line:#e6e6e6;
  --field:#c9c9c9;
  --dark:#1c1c1c;
  --white:#fff;
}
*{box-sizing:border-box;margin:0;padding:0}
html,body{width:1200px;height:3291px;overflow:hidden;background:var(--white)}
body{font-family:'Raleway',sans-serif;color:var(--ink);position:relative}
.center{text-align:center}

/* header */
.site-header{position:absolute;left:0;top:0;width:1200px;height:73px;background:var(--white);display:flex;align-items:center;padding:0 110px}
.brand{display:flex;align-items:center;gap:12px;font-weight:700;font-size:34px;color:var(--ink)}
.brand-square{width:40px;height:40px;background:var(--orange)}
.main-nav{margin-left:auto;display:flex;gap:46px;font-size:13px;font-weight:500;align-items:center}
.main-nav a{color:var(--ink);text-decoration:none}
.main-nav a.active{color:var(--orange)}

/* hero */
.hero{position:absolute;left:0;top:73px;width:1200px;height:400px;background:linear-gradient(90deg,#0d0d0d 0%,#2a2622 40%,#5b4c40 70%,#3a3430 100%);color:var(--white)}
.hero h1{position:absolute;top:124px;width:100%;font-weight:400;font-size:33px}
.hero p{position:absolute;top:196px;width:100%;font-size:24px;line-height:40px;font-weight:400}
.hero .arrow{position:absolute;top:180px}
.hero-badge{position:absolute;left:578px;top:450px;width:44px;height:44px;border-radius:50%;background:var(--orange);border:4px solid var(--white)}

/* section headings */
.section-title{position:absolute;width:100%;text-align:center;color:var(--orange);font-size:25px;font-weight:600}
.rule{position:absolute;left:110px;width:980px;height:2px;background:#f5c08a}
.small-rule{position:absolute;left:520px;width:160px;height:2px;background:#f5c08a}

.welcome-sub{position:absolute;top:566px;width:100%;text-align:center;font-size:17px;color:var(--ink)}
.welcome-text{position:absolute;top:645px;left:170px;width:860px;text-align:center;font-size:12px;line-height:28px;color:var(--muted)}

/* features */
.feature{position:absolute;font-size:12px;line-height:25px;color:var(--muted)}
.feature.left{left:110px;width:300px}
.feature.right{left:780px;width:300px}
.feat-icon{position:absolute;width:16px;height:16px}
.feature-visual{position:absolute;left:480px;top:870px;width:240px;height:325px;background:linear-gradient(160deg,#4a4a4a,#8a8a8a 55%,#3a3a3a)}
.btn{position:absolute;background:var(--orange);color:var(--white);border-radius:6px;font-size:15px;font-weight:500;text-align:center}

/* sample apps */
.apps{position:absolute;left:0;top:1332px;width:1200px;height:292px;background:linear-gradient(90deg,#1a1a1a 0%,#2d2a27 45%,#6a5b4e 75%,#3b3532 100%)}
.apps h2{position:absolute;left:185px;top:64px;color:var(--white);font-size:56px;line-height:72px;font-weight:700}
.store{position:absolute;top:124px;height:58px;background:#000;border:1px solid #777;border-radius:8px;color:var(--white);padding:8px 14px 0 48px}
.store small{display:block;font-size:10px}
.store b{font-size:22px;font-weight:500}
.store i{position:absolute;left:12px;top:14px;width:26px;height:26px;background:#ddd;border-radius:4px}

/* partners */
.partners{position:absolute;left:0;top:1624px;width:1200px;height:150px;display:flex;justify-content:space-around;align-items:center;padding:0 90px}
.partner{display:flex;align-items:center;gap:10px;font-size:36px;font-weight:600;color:#555}
.partner .dot{width:30px;height:30px;border-radius:50%;background:#9ab13a}

/* native push */
.push{position:absolute;left:0;top:1773px;width:1200px;height:427px;background:linear-gradient(90deg,var(--orange) 0%,var(--orange-dark) 58%,#3a3027 60%,#5a4a3d 100%)}
.push h3{position:absolute;right:615px;top:60px;color:var(--white);font-size:25px;font-weight:600}
.push ul{position:absolute;right:620px;top:105px;width:500px;list-style:none;color:var(--white);font-size:12px;line-height:25px;text-align:right}
.push li{margin-bottom:20px}
.push li::after{content:" «";font-weight:700;margin-left:14px}
.push-visual{position:absolute;left:630px;top:30px;width:290px;height:365px;background:linear-gradient(135deg,#d8d8d8 0%,#8fb9cc 45%,#2c2c2c 100%)}

/* speakers */
.speaker{position:absolute;top:2315px;width:242px;height:268px;background:#bdb6ad;border:1px solid #ddd}
.speaker .name{position:absolute;left:14px;bottom:44px;color:var(--white);font-size:16px;font-weight:600}
.speaker .role{position:absolute;left:14px;bottom:22px;color:var(--white);font-size:13px}
.slider-arrow{position:absolute;top:2445px}

/* contact */
.field{position:absolute;height:48px;border:2px solid var(--field);font-size:13px;color:#aaa;padding:13px 12px}
.field svg{position:absolute;right:12px;top:12px}

/* footer */
.site-footer{position:absolute;left:0;top:3054px;width:1200px;height:237px;background:var(--orange);color:var(--white)}
.social{position:absolute;top:37px;left:0;width:100%;display:flex;justify-content:center;gap:26px}
.social span{width:54px;height:54px;border-radius:50%;border:3px solid var(--white)}
.foot-rule{position:absolute;left:483px;top:130px;width:234px;height:1px;background:rgba(255,255,255,.5)}
.foot-nav{position:absolute;top:150px;width:100%;display:flex;justify-content:center;gap:68px;font-size:12px}
.copyright{position:absolute;top:187px;width:100%;text-align:center;font-size:12px}
</style>
</head>
<body>

<header class="site-header">
  <div class="brand"><span class="brand-square"></span>velmora</div>
  <nav class="main-nav">
    <a class="active" href="#">Home</a><a href="#">Product</a><a href="#">Contact</a><a href="#">Blog</a><a href="#">About</a><a href="#">Login</a>
    <svg width="14" height="14" viewBox="0 0 14 14"><circle cx="6" cy="6" r="4.5" fill="none" stroke="#f78f20" stroke-width="2"/><line x1="9.5" y1="9.5" x2="13" y2="13" stroke="#f78f20" stroke-width="2"/></svg>
  </nav>
</header>

<section class="hero" role="img" aria-label="Photo of a person watching video on a smartphone">
  <h1 class="center">High Quality Mobile Engagement™</h1>
  <p class="center">We engage mobile audiences with the right video<br>content at the perfect moment.</p>
  <svg class="arrow" style="left:40px" width="20" height="36" viewBox="0 0 20 36"><polyline points="18,2 2,18 18,34" fill="none" stroke="#fff" stroke-width="2"/></svg>
  <svg class="arrow" style="left:1140px" width="20" height="36" viewBox="0 0 20 36"><polyline points="2,2 18,18 2,34" fill="none" stroke="#fff" stroke-width="2"/></svg>
</section>
<div class="hero-badge"></div>

<h2 class="section-title" style="top:518px">Welcome To Velmora Media</h2>
<p class="welcome-sub">Ea esse efficiantur ex. Equidem volumus et mea, quo appareat causae diceret</p>
<div class="small-rule" style="top:615px"></div>
<p class="welcome-text">Congue verterem periculis no vim. Ne usu eruditi utroque corpora, ut ferri delenit laboramus vix. Eum ex agam labores cotidieque, pro eu vocent singulis. Idque affert dolorem nec id. Ei per civibus propriae assueverit. Id sed tuptatum inimicus consequat, duo regione definiebas eu. Omnis meliore qui cu, ad possit nonumes feugait usu. Vix quas prompta perfecto id, nobis prompta sanctus pro no. Ei malorum pertinacia ius. At posse graece utamur duo.</p>
<div class="rule" style="top:772px"></div>

<h2 class="section-title" style="top:810px">Features Of Velmora Media</h2>

<p class="feature left" style="top:925px">One of the common solutions is a "value exchange", where the consumers receive data or dollars off their bill, in exchange for viewing promotional content</p>
<p class="feature left" style="top:1025px">The type of content we see as most effective is native vertical video. Think of Flickpost 3V ads, but published directly to the phone, rather than a</p>
<p class="feature left" style="top:1125px">Videos are revealed at the right moment based on behavioral models that are built on the device.</p>
<svg class="feat-icon" style="left:452px;top:935px" viewBox="0 0 16 16"><polygon points="12,2 4,8 12,14" fill="#f78f20"/><rect x="13" y="2" width="2" height="12" fill="#f78f20"/></svg>
<svg class="feat-icon" style="left:452px;top:1035px" viewBox="0 0 16 16"><polygon points="12,2 4,8 12,14" fill="#f78f20"/><rect x="13" y="2" width="2" height="12" fill="#f78f20"/></svg>
<svg class="feat-icon" style="left:452px;top:1135px" viewBox="0 0 16 16"><polygon points="12,2 4,8 12,14" fill="#f78f20"/><rect x="13" y="2" width="2" height="12" fill="#f78f20"/></svg>

<div class="feature-visual" role="img" aria-label="Photo of two smartphones showing the video app"></div>

<svg class="feat-icon" style="left:740px;top:942px" viewBox="0 0 16 16"><rect x="1" y="2" width="2" height="12" fill="#f78f20"/><polygon points="4,2 12,8 4,14" fill="#f78f20"/></svg>
<svg class="feat-icon" style="left:740px;top:995px" viewBox="0 0 16 16"><rect x="1" y="2" width="2" height="12" fill="#f78f20"/><polygon points="4,2 12,8 4,14" fill="#f78f20"/></svg>
<svg class="feat-icon" style="left:740px;top:1120px" viewBox="0 0 16 16"><rect x="1" y="2" width="2" height="12" fill="#f78f20"/><polygon points="4,2 12,8 4,14" fill="#f78f20"/></svg>
<p class="feature right" style="top:937px">Increase ARPU with new revenue streams.</p>
<p class="feature right" style="top:990px">Velmora Media is a content platform(Not really but sounds better than "publisher". Need to workshop this.) for operators, that allows them to create new business models based on mobile video.</p>
<p class="feature right" style="top:1115px">Velmora's platforms predictively pre-positions video content, and uses ML to reveal video at the perfect moment for maximum engagement.</p>

<div class="btn" style="left:518px;top:1246px;width:164px;height:40px;line-height:40px">View All Info</div>

<section class="apps" role="img" aria-label="Photo of a hand holding a phone playing video">
  <h2>Our Sample<br>Apps</h2>
  <div class="store" style="left:630px;width:196px"><i></i><small>Available on the</small><b>AppVault</b></div>
  <div class="store" style="left:852px;width:200px"><i></i><small>Get it on</small><b>DroidMart</b></div>
</section>

<section class="partners">
  <div class="partner"><span class="dot"></span>Tessmark</div>
  <div class="partner">Brindal</div>
  <div class="partner">Quorra</div>
  <div class="partner">Harlune</div>
</section>

<section class="push">
  <h3>Native Push Video</h3>
  <ul>
    <li>Personalised flawless HD videos, discoverable in-app, and playable even when offline</li>
    <li>Guarantee your audience never gets frustrated with a poor quality mobile<br>video streaming experience.</li>
    <li>Instant video playback, zero buffering, HD quality guaranteed - even when offline</li>
    <li>Content is personalised based on viewer interests and mobile viewing habits</li>
    <li>Monetize with beautiful HD preroll or interstitial ads</li>
    <li>Use your existing content management and hosting systems</li>
  </ul>
  <div class="push-visual" role="img" aria-label="Photo of two smartphones showing a list of video trailers"></div>
</section>

<h2 class="section-title" style="top:2245px">Our Speakers</h2>
<svg class="slider-arrow" style="left:40px" width="20" height="40" viewBox="0 0 20 40"><polyline points="18,2 2,20 18,38" fill="none" stroke="#999" stroke-width="2"/></svg>
<svg class="slider-arrow" style="left:1140px" width="20" height="40" viewBox="0 0 20 40"><polyline points="2,2 18,20 2,38" fill="none" stroke="#999" stroke-width="2"/></svg>
<div class="speaker" style="left:98px" role="img" aria-label="Portrait photo of speaker Daniel"><span class="name">Daniel</span><span class="role">Mel in viris solet ut epicureiusto</span></div>
<div class="speaker" style="left:358px" role="img" aria-label="Portrait photo of speaker Greg"><span class="name">Greg</span><span class="role">Mel in viris solet ut epicureiusto</span></div>
<div class="speaker" style="left:608px" role="img" aria-label="Portrait photo of speaker Anders"><span class="name">Anders</span><span class="role">Mel in viris solet ut epicureiusto</span></div>
<div class="speaker" style="left:860px" role="img" aria-label="Portrait photo of speaker Martin Lead"><span class="name">Martin Lead</span><span class="role">Mel in viris solet ut epicureiusto</span></div>

<div class="rule" style="top:2637px"></div>
<h2 class="section-title" style="top:2670px">Contact Us</h2>

<div class="field" style="left:143px;top:2743px;width:450px">First &amp; Last name
  <svg width="22" height="22" viewBox="0 0 22 22"><circle cx="11" cy="7" r="5" fill="#ccc"/><path d="M2 21c0-6 4-8 9-8s9 2 9 8z" fill="#ccc"/></svg></div>
<div class="field" style="left:143px;top:2805px;width:450px">Phone No.
  <svg width="22" height="22" viewBox="0 0 22 22"><path d="M5 2l4 4-2 3c1 3 3 5 6 6l3-2 4 4-3 3C9 20 2 13 2 5z" fill="#ccc"/></svg></div>
<div class="field" style="left:143px;top:2867px;width:450px">Address
  <svg width="22" height="22" viewBox="0 0 22 22"><path d="M11 1a7 7 0 0 0-7 7c0 5 7 13 7 13s7-8 7-13a7 7 0 0 0-7-7z" fill="#ccc"/><circle cx="11" cy="8" r="2.5" fill="#fff"/></svg></div>
<div class="field" style="left:623px;top:2743px;width:452px">Postal Code</div>
<div class="field" style="left:623px;top:2805px;width:452px;height:110px">Your message</div>
<div class="btn" style="left:530px;top:2962px;width:156px;height:44px;line-height:44px;border-radius:10px">Contact Now</div>

<footer class="site-footer">
  <div class="social">
    <span role="img" aria-label="Social link"></span><span role="img" aria-label="Social link"></span><span role="img" aria-label="RSS feed"></span><span role="img" aria-label="Social link"></span>
  </div>
  <div class="foot-rule"></div>
  <nav class="foot-nav"><span>Home</span><span>Product</span><span>Contact</span><span>Blog</span><span>About</span><span>Login</span></nav>
  <p class="copyright">All Rights Reserved , Copyrights©velmora.tv</p>
</footer>

</body>
</html>
```